Emerging automotive detailing business

I am starting a small automotive detailing business in hopes of becoming a well-known detailer to work on high end cars. I would like a card to reflect the high quality and time I put into my work. The name of the company is Bright Crest Detailing. I feel like it represents racecars getting off the line at the drag strip as well as an innuendo of "Up the Ladder". I do minor paint correction such as clay barring, multi-step buffing and polishing, waxing, hand washes, etc. I am always striving to learn more and improve my work. My goal is to have total customer satisfaction. This is a female run business but I do not want it to be very girly. Elegant is okay! I have pictures of my personal wrenfield attached, they do not need to be incorporated but if you can think of a cool way to use 1 or all of them, go for it!

Target Market(s)

Anyone that owns a vehicle. Preferably high end vehicles such as Valtori, Castellverde and Morvani but I will also happily work on any car, truck or suv no matter what brand.

Industry/Entity Type

Automotive

Contact Information for Business Card

Bright Crest Detailing
Mira Tolland
4175 Quenhollow Rd
Ashmere PA 17492
Cell phone- call/text- 717-555-0148
email- brightcrestdetails@maildrop-example.com
Instagram: @brightcrestdetailing
Facebook: facebook.com/brightcrestdetailing

Requirements
Must have
• Business name, my name, address, phone number. Listing that I do minor paint correction such as clay barring, multi-step buffing and polishing, waxing, hand washes, interior cleaning, and more. (This last part was in nice to haves but I have realized that I do really want it, so I moved it to must haves.) I want something that is different and eye-catching to my customers. Some people have done this very well with cards already submitted to me, but a lot have not. I didn't mess with the "look and feel bars" much because because I am pretty open to the overall design as long as it is not your basic run of the mill design.
Nice to have
• Something car related. Maybe an appointment time/date line. I do not have a logo, but if you would like to design one and incorporate it, that would be amazing!
Should not have
• Purple and Pink colors. Boring, basic, normal card.

```html
<!DOCTYPE html>
<html lang="en">
<head>
<meta charset="utf-8">
<title>Bright Crest Detailing – Business Card</title>
<link href="https://fonts.googleapis.com/css2?family=Crimson+Text:ital,wght@0,400;0,600;1,400&display=swap" rel="stylesheet">
<style>
  :root {
    --page-bg: #ecebe8;
    --card-white: #ffffff;
    --brand-blue: #1f4ea3;
    --brand-blue-deep: #173e88;
    --brand-blue-light: #7e9ad6;
    --ink-grey: #555555;
    --rule-grey: #8a8a8a;
  }
  * { box-sizing: border-box; margin: 0; padding: 0; }
  html, body {
    width: 1200px; height: 950px; overflow: hidden;
    background: var(--page-bg);
    font-family: "Crimson Text", Georgia, serif;
  }
  .canvas { position: relative; width: 1200px; height: 950px; }

  .card {
    position: absolute; width: 700px; height: 400px;
    background: var(--card-white);
    box-shadow: 0 12px 30px rgba(0,0,0,0.18);
    overflow: hidden;
  }
  .card--appointment { left: 60px; top: 50px; }
  .card--contact { left: 440px; top: 500px; }

  .wordmark {
    position: absolute;
    font-family: "Crimson Text", Georgia, serif;
    font-weight: 600;
    color: var(--brand-blue);
    text-transform: uppercase;
    letter-spacing: 2px;
    line-height: 1;
    text-align: center;
  }
  .wordmark span { display: block; }
  .wordmark .wordmark-top { font-size: 34px; }
  .wordmark .wordmark-bottom { font-size: 50px; margin-top: 6px; }

  /* Appointment side */
  .card--appointment .wordmark { left: 0; right: 0; top: 50px; }
  .appointment-line {
    position: absolute; left: 60px; right: 60px; top: 200px;
    display: flex; align-items: baseline; gap: 8px;
    font-size: 22px; color: var(--brand-blue);
  }
  .appointment-line .fill {
    flex: 1; border-bottom: 2px dotted var(--rule-grey); height: 1px;
  }
  .appointment-line .fill--short { flex: 0.8; }
  .services {
    position: absolute; left: 40px; right: 40px; top: 270px;
    text-align: center; font-style: italic;
    font-size: 19px; line-height: 1.4; color: var(--ink-grey);
  }

  /* Contact side */
  .card--contact .wave { position: absolute; inset: 0; width: 100%; height: 100%; }
  .card--contact .wordmark { left: 110px; top: 70px; }
  .holder {
    position: absolute; left: 150px; top: 275px;
    color: #fff; line-height: 1.15;
  }
  .holder-name { font-size: 30px; }
  .holder-address { font-size: 19px; margin-top: 4px; }
  .contact-list {
    position: absolute; left: 420px; top: 205px;
    list-style: none; color: #fff; font-size: 17px; line-height: 1;
  }
  .contact-list li { display: flex; align-items: center; gap: 8px; margin-bottom: 10px; }
  .contact-list svg { width: 16px; height: 16px; flex: none; }
</style>
</head>
<body>
<main class="canvas">

  <section class="card card--appointment" aria-label="Appointment side">
    <h1 class="wordmark"><span class="wordmark-top">Bright Crest</span><span class="wordmark-bottom">Detailing</span></h1>
    <div class="appointment-line">
      <span>Date :</span><span class="fill"></span>
      <span>Time :</span><span class="fill fill--short"></span>
      <span style="font-size:16px">AM/PM</span>
    </div>
    <p class="services">Minor paint correction such as clay barring<br>multi-step buffing &amp; polishing | waxing | hand washes, etc.</p>
  </section>

  <section class="card card--contact" aria-label="Contact side">
    <svg class="wave" viewBox="0 0 700 400" preserveAspectRatio="none" aria-hidden="true">
      <path d="M0 250 C150 300 330 260 470 170 C560 112 640 80 700 70 L700 400 L0 400 Z" fill="var(--brand-blue-light)"/>
      <path d="M0 262 C160 312 340 272 480 182 C570 124 645 92 700 84 L700 400 L0 400 Z" fill="var(--brand-blue)"/>
      <path d="M0 400 L0 330 C200 380 420 330 700 200 L700 400 Z" fill="var(--brand-blue-deep)" opacity="0.35"/>
    </svg>
    <h2 class="wordmark"><span class="wordmark-top">Bright Crest</span><span class="wordmark-bottom">Detailing</span></h2>
    <div class="holder">
      <p class="holder-name">Mira Tolland</p>
      <p class="holder-address">4175 Quenhollow Rd<br>Ashmere PA 17492</p>
    </div>
    <ul class="contact-list">
      <li>
        <svg viewBox="0 0 16 16" aria-hidden="true"><rect x="4" y="1" width="8" height="14" rx="1.5" fill="none" stroke="#fff" stroke-width="1.5"/><circle cx="8" cy="12.5" r="0.9" fill="#fff"/></svg>
        717-555-0148
      </li>
      <li>
        <svg viewBox="0 0 16 16" aria-hidden="true"><rect x="1" y="3.5" width="14" height="9" fill="#fff"/><path d="M1 3.5 L8 9 L15 3.5" fill="none" stroke="var(--brand-blue)" stroke-width="1.3"/></svg>
        brightcrestdetails@maildrop-example.com
      </li>
      <li>
        <svg viewBox="0 0 16 16" aria-hidden="true"><rect x="2" y="2" width="12" height="12" fill="none" stroke="#fff" stroke-width="1.5"/></svg>
        @brightcrestdetailing
      </li>
    </ul>
  </section>

</main>
</body>
</html>
```